FinTech company looking to revamp and expand client-facing interface for our financial models

Pellworth Engines currently has a very simple website that allows clients to interact with our financial models. We are looking to completely redesign the current site and add several extra pages to provide extra functionality. We want the design to have a modern, slick feel, that will work on both a desktop or a tablet. It should be straightforward for clients to move between different pages at any time, and clear from the layout how to interact with the more advanced features. We have included screenshots of existing pages in the attached design brief, as well as sketches of the functionality required by the new pages, but can't provide a direct link to the current site.
Target Market(s)
Professional investors that will be paying to access the interface
Industry/Entity Type
Finance
Number of Pages Required
4 page
Colors
Designer to choose colors to be used in the design.
Look and feel
Each slider illustrates characteristics of the customer's brand and the style your logo design should communicate.

```html
<!DOCTYPE html>
<html lang="en">
<head>
<meta charset="utf-8">
<title>QORVEL – Models</title>
<link href="https://fonts.googleapis.com/css2?family=Roboto:wght@400;500&display=swap" rel="stylesheet">
<style>
:root{
  --blue:#1e88e5;
  --page:#f7f7f7;
  --white:#ffffff;
  --ink:#333a44;
  --muted:#8b9bb0;
  --faint:#b4c0cf;
  --row-alt:#f5f8fd;
  --star:#c3ccd8;
  --fav:#e53935;
}
*{box-sizing:border-box;margin:0;padding:0}
html,body{width:1200px;height:676px;overflow:hidden}
body{background:var(--page);font-family:'Roboto',sans-serif;color:var(--ink);position:relative}

.topbar{position:absolute;left:0;top:0;width:1200px;height:67px;background:var(--white);box-shadow:0 2px 8px rgba(0,0,0,.03)}
.brand{position:absolute;left:150px;top:18px;font-size:22px;font-weight:500;color:#2d2d2d;letter-spacing:.5px}
.horizon{position:absolute;top:0;height:67px;line-height:67px;font-size:12.5px;color:#2d2d2d;text-align:center}
.horizon.active{background:var(--blue);color:var(--white)}
.nav-item{position:absolute;top:0;height:67px;display:flex;align-items:center;gap:6px;font-size:13px;color:#2d2d2d}
.nav-item svg{width:18px;height:18px}
.nav-item.active{color:var(--blue)}
.nav-item.active::after{content:"";position:absolute;left:-13px;right:-15px;bottom:0;height:2px;background:var(--blue)}

.filter-tab{position:absolute;left:0;top:118px;width:34px;height:82px;background:var(--blue);border-radius:0 3px 3px 0;color:var(--white)}
.filter-tab span{position:absolute;left:8px;top:44px;transform:rotate(-90deg);transform-origin:left top;font-size:12px;font-weight:500}
.filter-tab svg{position:absolute;left:8px;top:52px;width:16px;height:16px}

.asset-tabs{position:absolute;left:148px;top:118px;height:27px}
.asset-tab{position:absolute;top:0;height:27px;line-height:27px;font-size:12px;color:var(--faint);white-space:nowrap}
.asset-tab.active{background:var(--blue);color:var(--white);border-radius:14px;width:83px;text-align:center}
.export{position:absolute;left:996px;top:121px;display:flex;align-items:center;gap:5px;color:var(--blue);font-size:12px;font-weight:500}
.export svg{width:14px;height:14px}

.models-table{position:absolute;left:150px;top:156px;width:900px;background:var(--white);border-radius:4px;box-shadow:0 2px 10px rgba(60,90,130,.06);overflow:hidden}
.row{display:grid;grid-template-columns:92px 82px 89px 80px 70px 68px 69px 73px 72px 69px 67px 69px;align-items:center}
.row.head{height:45px;background:var(--row-alt);color:var(--muted);font-size:12.5px}
.row.body{height:70px;font-size:12.5px}
.row.body:nth-child(odd){background:var(--row-alt)}
.row > div:first-child{padding-left:10px;display:flex;align-items:center;gap:6px}
.row.head > div:first-child{padding-left:14px}
.star{width:9px;height:9px}
.time{line-height:15.5px}
.num-l{margin-left:-2px}
</style>
</head>
<body>
<header class="topbar">
  <div class="brand">QORVEL</div>
  <div class="horizon active" style="left:262px;width:60px">250D</div>
  <div class="horizon" style="left:336px;width:32px">83D</div>
  <div class="horizon" style="left:394px;width:32px">42D</div>

  <div class="nav-item active" style="left:551px">
    <svg viewBox="0 0 20 20" fill="none" stroke="currentColor" stroke-width="1.5"><path d="M3 9 L10 3 L17 9 V17 H3 Z"/></svg>Models
  </div>
  <div class="nav-item" style="left:656px">
    <svg viewBox="0 0 20 20" fill="none" stroke="currentColor" stroke-width="1.4"><circle cx="4" cy="4" r="1.8"/><circle cx="10" cy="4" r="1.8"/><circle cx="16" cy="4" r="1.8"/><circle cx="4" cy="10" r="1.8"/><circle cx="10" cy="10" r="1.8"/><circle cx="16" cy="10" r="1.8"/><circle cx="10" cy="16" r="1.8"/></svg>Portfolio Builder
  </div>
  <div class="nav-item" style="left:815px">
    <svg viewBox="0 0 20 20" fill="none" stroke="currentColor" stroke-width="1.6"><path d="M10 3 L18 7.5 L10 12 L2 7.5 Z"/><path d="M2 11.5 L10 16 L18 11.5"/></svg>Sensitivities
  </div>
  <div class="nav-item" style="left:952px">
    <svg viewBox="0 0 20 20" fill="none" stroke="currentColor" stroke-width="1.5"><path d="M10 2 L12.4 7.3 L18 7.8 L13.7 11.5 L15 17 L10 14.1 L5 17 L6.3 11.5 L2 7.8 L7.6 7.3 Z"/></svg>Favourites
  </div>
</header>

<div class="filter-tab">
  <span>Filter</span>
  <svg viewBox="0 0 16 16" fill="none" stroke="currentColor" stroke-width="1.4"><rect x="1.5" y="2" width="5" height="12" rx="2.5"/><rect x="9.5" y="2" width="5" height="12" rx="2.5"/><path d="M1.5 8 H6.5 M9.5 8 H14.5"/></svg>
</div>

<nav class="asset-tabs">
  <div class="asset-tab active" style="left:0">EQUITIES</div>
  <div class="asset-tab" style="left:114px">ETFS</div>
  <div class="asset-tab" style="left:189px">PAIRS</div>
  <div class="asset-tab" style="left:270px">ETF PAIRS</div>
  <div class="asset-tab" style="left:373px">FACTORS</div>
</nav>
<div class="export">
  <svg viewBox="0 0 16 16" fill="none" stroke="currentColor" stroke-width="1.6"><path d="M12 9 V14 H2 V4 H7"/><path d="M9 2 H14 V7 M14 2 L7 9"/></svg>Export
</div>

<section class="models-table">
  <div class="row head">
    <div>ID <svg width="8" height="8" viewBox="0 0 8 8" fill="none" stroke="currentColor" stroke-width="1.2"><path d="M1.5 3 L4 5.5 L6.5 3"/></svg></div>
    <div>Sector</div><div>Time</div><div>Quality</div>
    <div>Stat 1</div><div>Stat 2</div><div>Stat 3</div><div>Stat 4</div>
    <div>Stat 5</div><div>Stat 6</div><div>Stat 7</div><div>Stat 8</div>
  </div>

  <div class="row body">
    <div><svg class="star" viewBox="0 0 20 20" fill="none" stroke="var(--star)" stroke-width="1.6"><path d="M10 2 L12.4 7.3 L18 7.8 L13.7 11.5 L15 17 L10 14.1 L5 17 L6.3 11.5 L2 7.8 L7.6 7.3 Z"/></svg>Model 1</div>
    <div>Materials</div><div class="time">2019-07-03<br>12:15:00.000</div><div>30.2888</div>
    <div>2.01574</div><div class="num-l">23.305</div><div class="num-l">-0.149368</div><div class="num-l">22.3054</div>
    <div>4.63714</div><div>0.945706</div><div>2.81949</div><div>2.60858</div>
  </div>
  <div class="row body">
    <div><svg class="star" viewBox="0 0 20 20" fill="var(--fav)"><path d="M10 2 L12.4 7.3 L18 7.8 L13.7 11.5 L15 17 L10 14.1 L5 17 L6.3 11.5 L2 7.8 L7.6 7.3 Z"/></svg>Model 2</div>
    <div>Materials</div><div class="time">2019-07-03<br>12:15:00.000</div><div>30.2888</div>
    <div>2.01574</div><div class="num-l">23.305</div><div class="num-l">-0.149368</div><div class="num-l">22.3054</div>
    <div>4.63714</div><div>0.945706</div><div>2.81949</div><div>2.60858</div>
  </div>
  <div class="row body">
    <div><svg class="star" viewBox="0 0 20 20" fill="none" stroke="var(--star)" stroke-width="1.6"><path d="M10 2 L12.4 7.3 L18 7.8 L13.7 11.5 L15 17 L10 14.1 L5 17 L6.3 11.5 L2 7.8 L7.6 7.3 Z"/></svg>Model 3</div>
    <div>Materials</div><div class="time">2019-07-03<br>12:15:00.000</div><div>30.2888</div>
    <div>2.01574</div><div class="num-l">23.305</div><div class="num-l">-0.149368</div><div class="num-l">22.3054</div>
    <div>4.63714</div><div>0.945706</div><div>2.81949</div><div>2.60858</div>
  </div>
  <div class="row body">
    <div><svg class="star" viewBox="0 0 20 20" fill="none" stroke="var(--star)" stroke-width="1.6"><path d="M10 2 L12.4 7.3 L18 7.8 L13.7 11.5 L15 17 L10 14.1 L5 17 L6.3 11.5 L2 7.8 L7.6 7.3 Z"/></svg>Model 4</div>
    <div>Materials</div><div class="time">2019-07-03<br>12:15:00.000</div><div>30.2888</div>
    <div>2.01574</div><div class="num-l">23.305</div><div class="num-l">-0.149368</div><div class="num-l">22.3054</div>
    <div>4.63714</div><div>0.945706</div><div>2.81949</div><div>2.60858</div>
  </div>
  <div class="row body">
    <div><svg class="star" viewBox="0 0 20 20" fill="none" stroke="var(--star)" stroke-width="1.6"><path d="M10 2 L12.4 7.3 L18 7.8 L13.7 11.5 L15 17 L10 14.1 L5 17 L6.3 11.5 L2 7.8 L7.6 7.3 Z"/></svg>Model 5</div>
    <div>Materials</div><div class="time">2019-07-03<br>12:15:00.000</div><div>30.2888</div>
    <div>2.01574</div><div class="num-l">23.305</div><div class="num-l">-0.149368</div><div class="num-l">22.3054</div>
    <div>4.63714</div><div>0.945706</div><div>2.81949</div><div>2.60858</div>
  </div>
  <div class="row body">
    <div><svg class="star" viewBox="0 0 20 20" fill="none" stroke="var(--star)" stroke-width="1.6"><path d="M10 2 L12.4 7.3 L18 7.8 L13.7 11.5 L15 17 L10 14.1 L5 17 L6.3 11.5 L2 7.8 L7.6 7.3 Z"/></svg>Model 6</div>
    <div>Materials</div><div class="time">2019-07-03<br>12:15:00.000</div><div>30.2888</div>
    <div>2.01574</div><div class="num-l">23.305</div><div class="num-l">-0.149368</div><div class="num-l">22.3054</div>
    <div>4.63714</div><div>0.945706</div><div>2.81949</div><div>2.60858</div>
  </div>
</section>
</body>
</html>
```